Kampfsport Außenwerbung
Zielgruppe
Kampfsportschule für Kinder, Jugendliche und Erwachsene. Sportarten: Kick-Boxen, Jiu-Jitsu und Tricking
Aufgabenstellung
Ich bräuchte für meine Schaufenster eine schöne Außenwerbung. Beworben werden sollen alle meine Sportarten. Ich lade meinen Flyer hoch, damit im ähnlichen Stil gearbeitet werden kann. Außerdem auch noch andere Beispiele an denen man sich orientieren kann, sowie mein Logo und meine Fensterfront.

```html
<!DOCTYPE html>
<html lang="de">
<head>
<meta charset="utf-8">
<title>Martial Arts Borq – Schaufensterbeklebung</title>
<link href="https://fonts.googleapis.com/css2?family=Rubik:wght@500;700;800&family=EB+Garamond:wght@400;500&display=swap" rel="stylesheet">
<style>
  :root{
    --bg:#ebe9e6;
    --frame:#dfe2e5;
    --frame-edge:#c9cdd1;
    --panel-dark:#1f1f21;
    --panel-mid:#3a3a3d;
    --red:#a3121c;
    --red-dark:#6e0c13;
    --red-bright:#d71f26;
    --white:#ffffff;
    --glass:#c9c6c2;
    --sign:#f1f1f1;
    --ink:#1d1d1d;
    --gray-cell:#5d5d60;
    --light-cell:#9b9b9e;
  }
  *{box-sizing:border-box;margin:0;padding:0}
  html,body{width:900px;height:1200px;overflow:hidden}
  body{background:var(--bg);font-family:"Rubik",Arial,sans-serif;position:relative}

  .storefront{position:absolute;left:14px;top:322px;width:872px;height:552px;background:var(--frame);border:1px solid var(--frame-edge)}
  .pane{position:absolute;overflow:hidden;
    background:
      radial-gradient(ellipse 70% 30% at 50% 8%, rgba(150,20,28,.45), transparent 70%),
      radial-gradient(ellipse 90% 60% at 50% 55%, var(--panel-mid), var(--panel-dark) 80%);
    color:var(--white)}
  .pane .shout{position:absolute;left:0;right:0;text-align:center;font-weight:700;text-shadow:0 1px 3px rgba(0,0,0,.8)}

  .brand-mark{position:absolute;left:0;right:0;display:flex;align-items:center;justify-content:center;gap:5px;font-weight:700;color:var(--red)}
  .brand-mark .dot{width:9px;height:9px;border-radius:50%;background:currentColor;flex:none}

  .photo{position:absolute;border-radius:4px;
    background:radial-gradient(ellipse 60% 20% at 50% 96%, rgba(210,40,40,.55), transparent 70%),
               linear-gradient(180deg, rgba(70,70,74,.55), rgba(40,40,44,.55))}

  .band{position:absolute;left:0;width:100%}
  .band svg{display:block;width:100%;height:100%}
  .band-title{position:absolute;left:0;right:0;text-align:center;font-weight:800;color:var(--white);text-shadow:0 2px 3px rgba(0,0,0,.6);transform:rotate(-7deg)}

  /* transom sign */
  .entry-sign{position:absolute;top:14px;left:46px;width:200px;height:84px;background:var(--sign);
    border-top:3px solid var(--red);border-bottom:3px solid var(--red);display:flex;align-items:center;gap:8px;padding:0 10px}
  .entry-sign .seal{width:38px;height:38px;border-radius:50%;background:var(--red);flex:none}
  .entry-sign .name{font-weight:800;font-size:12px;letter-spacing:.5px;color:var(--ink)}
  .entry-sign .claim{font-family:"EB Garamond",Georgia,serif;font-size:11px;color:var(--ink);line-height:1.25;margin-top:3px;text-align:center}
  .glass{position:absolute;top:0;height:110px;background:linear-gradient(180deg,#d7d3cf,var(--glass))}

  /* door info */
  .info-title{font-size:14px;font-weight:700;top:24px;line-height:1.1}
  .info-rule{position:absolute;left:6px;right:6px;top:70px;height:2px;background:var(--red-bright)}
  .info-list{position:absolute;left:12px;right:6px;top:98px;font-size:8px;font-weight:500}
  .info-list h3{font-size:9.5px;font-weight:700;margin-bottom:12px;text-align:center}
  .info-list li{list-style:none;display:flex;align-items:center;gap:6px;margin-bottom:10px;font-size:7px}
  .info-list svg{width:10px;height:10px;flex:none}
  .lead{top:238px;font-size:10px;line-height:1.3}

  /* schedule */
  .schedule{position:absolute;left:6px;top:110px;width:150px;border-collapse:collapse;background:var(--white);font-size:3.8px;line-height:1.15;color:var(--ink);table-layout:fixed}
  .schedule th{background:var(--ink);color:var(--white);font-weight:700;padding:3px 0;font-size:3.6px}
  .schedule td{padding:1.5px 1px;border:.5px solid #ccc;text-align:left;height:15px;vertical-align:middle}
  .schedule .time{background:var(--red-bright);color:var(--white);width:15px;font-weight:700}
  .schedule .jj{background:var(--red-bright);color:var(--white)}
  .schedule .tr{background:var(--gray-cell);color:var(--white)}
  .schedule .u25{background:var(--light-cell);color:var(--white)}
</style>
</head>
<body>
<main class="storefront" aria-label="Schaufensterfront Martial Arts Borq">

  <!-- column 1 -->
  <section class="pane" style="left:6px;top:6px;width:112px;height:110px">
    <div class="brand-mark" style="top:46px;font-size:9px;opacity:.55"><span class="dot"></span>Martial Arts Borq</div>
  </section>
  <section class="pane" style="left:6px;top:124px;width:112px;height:420px">
    <div class="photo" role="img" aria-label="Foto: Kind mit Kopfschutz und Boxhandschuhen beim hohen Seitkick" style="left:8px;top:36px;width:96px;height:300px"></div>
    <div class="band" style="top:338px;height:82px">
      <svg viewBox="0 0 112 82" preserveAspectRatio="none"><polygon points="0,0 14,28 112,14 112,0 100,0 112,0" fill="var(--red-dark)"/><polygon points="0,44 112,20 112,66 0,82" fill="var(--red)"/></svg>
    </div>
    <div class="band-title" style="top:372px;font-size:15px">KICK-BOXEN</div>
  </section>

  <!-- column 2 -->
  <section class="pane" style="left:124px;top:6px;width:122px;height:110px">
    <p class="shout" style="top:44px;font-size:8px;line-height:1.35">Für Kinder, Jugendliche<br>und Erwachsene!</p>
  </section>
  <section class="pane" style="left:124px;top:124px;width:122px;height:420px">
    <div class="band" style="top:0;height:90px">
      <svg viewBox="0 0 122 90" preserveAspectRatio="none"><polygon points="0,30 18,54 0,70" fill="var(--red-dark)"/><polygon points="0,46 122,18 122,56 0,88" fill="var(--red)"/></svg>
    </div>
    <div class="band-title" style="top:42px;font-size:16px">JIU-JITSU</div>
    <div class="photo" role="img" aria-label="Foto: Kind im weißen Gi mit gelbem Gürtel" style="left:28px;top:110px;width:66px;height:290px"></div>
  </section>

  <!-- entrance transom -->
  <section style="position:absolute;left:252px;top:6px;width:290px;height:110px;background:var(--glass)">
    <div class="glass" style="left:0;width:44px"></div>
    <div class="glass" style="right:0;width:44px"></div>
    <div class="entry-sign">
      <span class="seal" aria-hidden="true"></span>
      <div>
        <div class="name">MARTIAL ARTS BORQ</div>
        <div class="claim">Kampfsport &amp;<br>Selbstverteidigung</div>
      </div>
    </div>
  </section>

  <!-- doors -->
  <section class="pane" style="left:252px;top:124px;width:142px;height:420px">
    <div class="brand-mark" style="top:150px;font-size:10px"><span class="dot"></span>Martial Arts Borq</div>
    <p class="shout" style="top:200px;font-size:14px;line-height:1.15">MARTIAL ARTS<br>BORQ</p>
    <div class="band" style="top:376px;height:44px">
      <svg viewBox="0 0 142 44" preserveAspectRatio="none"><polygon points="0,14 142,0 142,24 0,38" fill="var(--red)"/></svg>
    </div>
  </section>
  <section class="pane" style="left:400px;top:124px;width:142px;height:420px">
    <p class="shout info-title">MARTIAL ARTS<br>BORQ</p>
    <div class="info-rule"></div>
    <div class="info-list">
      <h3>INFO &amp; PROBETRAINING</h3>
      <ul>
        <li><svg viewBox="0 0 10 10"><rect x=".5" y="2" width="9" height="6.5" fill="none" stroke="var(--red-bright)"/><polyline points=".5,2 5,6 9.5,2" fill="none" stroke="var(--red-bright)"/></svg>info@martial-arts-borq.de</li>
        <li><svg viewBox="0 0 10 10"><circle cx="5" cy="5" r="4.3" fill="none" stroke="var(--red-bright)"/><path d="M3.4 3.1c.3-.3.7-.2.8.1l.4.8c.1.3-.2.5-.3.7.3.7.8 1.2 1.5 1.5.2-.1.4-.4.7-.3l.8.4c.3.1.4.5.1.8-.6.6-1.6.5-2.6-.3-.9-.8-1.6-1.7-1.8-2.6-.1-.5.1-.9.4-1.1z" fill="var(--red-bright)"/></svg>0152 / 3080 1946</li>
      </ul>
    </div>
    <p class="shout lead">LEITUNG:<br>TIMO BORQ</p>
    <div class="band" style="top:370px;height:50px">
      <svg viewBox="0 0 142 50" preserveAspectRatio="none"><polygon points="0,20 142,4 142,30 0,46" fill="var(--red)"/></svg>
    </div>
  </section>

  <!-- column 5 -->
  <section class="pane" style="left:548px;top:6px;width:150px;height:110px">
    <p class="shout" style="top:46px;font-size:9.5px;line-height:1.3">Wir machen Dich<br>Stark!</p>
  </section>
  <section class="pane" style="left:548px;top:124px;width:150px;height:420px">
    <div class="photo" role="img" aria-label="Foto: Kind im Stand-Spagat mit gelbem Gürtel" style="left:36px;top:30px;width:80px;height:300px"></div>
    <div class="band" style="top:312px;height:108px">
      <svg viewBox="0 0 150 108" preserveAspectRatio="none"><polygon points="150,0 150,40 128,30" fill="var(--red-dark)"/><polygon points="0,60 150,30 150,80 0,108" fill="var(--red)"/></svg>
    </div>
    <div class="band-title" style="top:354px;font-size:18px">TRICKING</div>
  </section>

  <!-- column 6 -->
  <section class="pane" style="left:704px;top:6px;width:162px;height:110px">
    <div class="brand-mark" style="top:46px;font-size:11px;opacity:.55"><span class="dot"></span>Martial Arts Borq</div>
  </section>
  <section class="pane" style="left:704px;top:124px;width:162px;height:420px">
    <div class="band" style="top:0;height:100px">
      <svg viewBox="0 0 162 100" preserveAspectRatio="none"><polygon points="0,18 24,46 0,58" fill="var(--red-dark)"/><polygon points="0,50 162,10 162,54 0,98" fill="var(--red)"/></svg>
    </div>
    <div class="band-title" style="top:30px;font-size:16px;line-height:1.05">TRAININGS-<br>PLAN</div>

    <table class="schedule">
      <thead>
        <tr><th></th><th>MONTAG</th><th>DIENSTAG</th><th>MITTWOCH</th><th>DONNERSTAG</th><th>FREITAG</th></tr>
      </thead>
      <tbody>
        <tr><td class="time">15:00<br>15:50</td><td>Kick-Boxen<br>3-5 Jahre</td><td class="jj">Jiu-Jitsu<br>3-6 Jahre</td><td>Kick-Boxen<br>3-5 Jahre</td><td class="jj">Jiu-Jitsu<br>3-6 Jahre</td><td></td></tr>
        <tr><td class="time">16:00<br>16:50</td><td>Kick-Boxen<br>6-7 Jahre</td><td class="jj">Jiu-Jitsu<br>7-12 Jahre</td><td>Kick-Boxen<br>6-7 Jahre</td><td class="jj">Jiu-Jitsu<br>7-12 Jahre</td><td>Kick-Boxen<br>3-5 Jahre</td></tr>
        <tr><td class="time">17:00<br>18:50</td><td>Kick-Boxen<br>8-10 Jahre</td><td class="tr">Tricking<br>ab 6 Jahre</td><td>Kick-Boxen<br>8-10 Jahre</td><td class="tr">Tricking<br>ab 6 Jahre</td><td>Kick-Boxen<br>ab 7 Jahre<br>Ab Gelbgurt</td></tr>
        <tr><td class="time">18:15<br>19:15</td><td>Kick-Boxen<br>10-12 Jahre</td><td class="u25">Kick-Boxen<br>U25 Gruppe</td><td>Kick-Boxen<br>10-12 Jahre</td><td class="u25">Kick-Boxen<br>U25 Gruppe</td><td></td></tr>
        <tr><td class="time">19:30<br>21:00</td><td>Kick-Boxen<br>ab 13 Jahre</td><td></td><td>Kick-Boxen<br>ab 13 Jahre</td><td></td><td></td></tr>
      </tbody>
    </table>

    <p class="shout" style="top:330px;font-size:11px;line-height:1.35">Jetzt Probetermin<br>vereinbaren!</p>
  </section>

</main>
</body>
</html>
```